Resposive web site in 4 languages + image gallery + logo design

We need a web page, which will work on all devices.
I have uploaded web page concept.
Company name: Praxelun
Industry/Entity Type
It Company
Logo Text
quality matters
Coding
Coded - Design and coding required
Number of Pages Required
1 page

```html
<!DOCTYPE html>
<html lang="en">
<head>
<meta charset="utf-8">
<title>Praxelun – Construction &amp; Renovation</title>
<link rel="stylesheet" href="https://fonts.googleapis.com/css2?family=Lato:wght@400;700&family=Philosopher:wght@400;700&display=swap">
<style>
:root{
  --orange:#f2672e;
  --black:#000;
  --ink:#222;
  --text:#444;
  --muted:#d0d0d0;
  --light:#e6e6e6;
  --band:#e8e8e8;
  --footer:#111;
  --white:#fff;
}
*{box-sizing:border-box;margin:0;padding:0}
html,body{width:1200px;height:2659px;overflow:hidden}
body{font-family:"Lato",sans-serif;color:var(--text);background:var(--white);position:relative}
.abs{position:absolute}
.head{font-family:"Philosopher",sans-serif;font-weight:400}

.topbar{top:0;left:0;width:1200px;height:43px;background:var(--light);font-size:14px;color:var(--orange)}
.topbar .contact{left:101px;top:12px;display:flex;gap:24px;align-items:center}
.topbar .contact span{display:flex;gap:8px;align-items:center}
.social{display:flex;gap:16px}
.social i{width:18px;height:18px;border-radius:50%;border:2px solid var(--orange);display:block}
.topbar .social{right:92px;top:12px}

.nav{top:43px;left:0;width:1200px;height:94px;background:var(--black)}
.brand{display:flex;align-items:center;gap:10px;color:var(--white);font-family:"Lato",sans-serif;font-weight:700}
.brand i{width:34px;height:34px;background:var(--orange);display:block}
.nav .brand{left:101px;top:28px;font-size:24px}
.nav .links{left:532px;top:38px;display:flex;font-size:14px;color:var(--orange)}
.nav .links a{color:inherit;text-decoration:none;position:absolute;white-space:nowrap}
.nav .dot{width:6px;height:6px;border-radius:50%;background:#555;position:absolute;top:6px}
.lang{left:989px;top:0;width:110px;height:94px;background:#1f1f1f;display:flex;align-items:center;justify-content:center;gap:8px;font-size:11px;color:#aaa}
.lang i{width:22px;height:14px;background:#2a3f86;display:block}

.hero{top:137px;left:0;width:1200px;height:473px;background:linear-gradient(120deg,#4a3a2a 0%,#8a6c4c 40%,#b08c64 60%,#5c4632 100%)}
.welcome{left:0;top:203px;width:532px;height:119px;background:rgba(0,0,0,.55);padding:18px 0 0 99px;color:var(--white)}
.welcome h1{font-size:39px;line-height:1.1}
.welcome p{font-size:13px;line-height:21px;margin-top:6px;color:#e5e5e5}

.estimate{top:610px;left:0;width:1200px;height:85px;background:var(--black)}
.estimate p{left:101px;top:30px;color:var(--white);font-size:19px}
.btn{background:var(--orange);color:var(--white);font-weight:700;border-radius:3px;display:flex;align-items:center;justify-content:center}
.estimate .btn{left:959px;top:25px;width:124px;height:33px;font-size:13px}

.services-title{top:760px;left:0;width:1200px;text-align:center}
.services-title h2{font-size:34px;color:var(--ink)}
.services-title h2 span{color:var(--orange)}
.services-title hr{width:88px;border:0;border-top:2px solid #999;margin:14px auto 0}

.photo{display:block}
.service h3{font-family:"Philosopher",sans-serif;font-weight:400;font-size:23px;color:var(--ink)}
.service hr{width:58px;border:0;border-top:2px solid var(--orange);margin:12px 0 16px}
.service p{font-size:13.3px;line-height:24.8px;width:482px}
.service .btn{width:94px;height:30px;font-size:13px;margin-top:18px}
.tags{left:0;width:1200px;display:flex;justify-content:center;gap:22px;font-size:16px;color:var(--ink)}
.tags span::before{content:"";display:inline-block;width:7px;height:7px;border-radius:50%;background:var(--ink);margin-right:9px;vertical-align:middle}

.stone-band{top:1232px;left:0;width:1200px;height:376px;background:var(--band)}

.about{top:1982px;left:0;width:1200px;height:375px;background:linear-gradient(100deg,#2a2a2a 0%,#333 50%,#3a3d40 75%,#2c2c2c 100%)}
.about h2{left:0;width:1200px;top:70px;text-align:center;font-size:33px;color:var(--white)}
.about .rule{left:556px;top:126px;width:88px;border-top:2px solid #bbb}
.about .brand{left:186px;top:190px;font-size:32px}
.about .brand i{width:48px;height:48px}
.about p{left:494px;top:160px;width:605px;font-size:13.3px;line-height:24.5px;color:#eee}
.about .sign{left:494px;top:292px;font-size:15px;color:var(--white);line-height:24px}

.footer{top:2357px;left:0;width:1200px;height:249px;background:var(--footer);color:#ddd;font-size:13.5px}
.footer .info{left:160px;top:40px;line-height:24px}
.footer .row{display:flex;gap:16px;align-items:flex-start;margin-bottom:12px}
.footer svg{flex:none;margin-top:5px}
.field{border:1px solid #555;background:#1a1a1a;color:#777;font-size:12px;padding:7px 10px}
.footer .submit{left:640px;top:148px;width:94px;height:30px;font-size:13px}
.footer .menu{left:948px;top:44px;line-height:35px}
.footer .menu div{padding-left:23px}

.copy{top:2606px;left:0;width:1200px;height:53px;background:var(--black);color:#ccc;font-size:12px}
.copy p{left:101px;top:19px}
.copy .social{right:92px;top:17px}
</style>
</head>
<body>

<div class="abs topbar">
  <div class="abs contact">
    <span><svg width="14" height="14" viewBox="0 0 24 24"><path fill="#f2672e" d="M6.6 10.8a15 15 0 0 0 6.6 6.6l2.2-2.2c.3-.3.7-.4 1-.2 1.1.4 2.3.6 3.6.6.6 0 1 .4 1 1V20c0 .6-.4 1-1 1A17 17 0 0 1 3 4c0-.6.4-1 1-1h3.5c.6 0 1 .4 1 1 0 1.3.2 2.5.6 3.6.1.3 0 .7-.2 1z"/></svg>555-201-4470</span>
    <span><svg width="16" height="12" viewBox="0 0 16 12"><rect x="1" y="1" width="14" height="10" fill="none" stroke="#f2672e" stroke-width="1.5"/><path d="M1 1l7 6 7-6" fill="none" stroke="#f2672e" stroke-width="1.5"/></svg>info@praxelun.com</span>
  </div>
  <div class="abs social"><i></i><i></i><i></i><i></i><i></i></div>
</div>

<header class="abs nav">
  <div class="abs brand"><i></i>Praxelun</div>
  <nav class="abs links">
    <a style="left:0">Home</a>
    <span class="dot" style="left:68px"></span>
    <a style="left:103px">About Us</a>
    <span class="dot" style="left:196px"></span>
    <a style="left:234px">Services</a>
    <span class="dot" style="left:319px"></span>
    <a style="left:354px">Contact Us</a>
  </nav>
  <div class="abs lang"><i></i>English ⌄</div>
</header>

<section class="abs hero" role="img" aria-label="Carpenter's hand marking a plank with a pencil among woodworking chisels">
  <div class="abs welcome">
    <h1 class="head">Welcome To Praxelun</h1>
    <p>Lorem ipsum dolor sit amet, consectetuer adipiscing elit, sed diam<br>nonummy nibh euismod tincidunt ut laoreet dolore magna aliquam</p>
  </div>
</section>

<section class="abs estimate">
  <p class="abs">Are you Interested in an Estimate?</p>
  <div class="abs btn">GET A QUOTE</div>
</section>

<div class="abs services-title">
  <h2 class="head">Our <span>Services</span></h2>
  <hr>
</div>

<div class="abs photo" style="top:863px;left:0;width:578px;height:294px;background:linear-gradient(110deg,#6b6e72 0%,#c9b79a 45%,#8a8f94 70%,#d8c9b0 100%)" role="img" aria-label="Carpenter cutting a board with a circular saw, with furniture and flooring details"></div>
<article class="abs service" style="top:888px;left:620px">
  <h3>Wood Works</h3><hr>
  <p>Timber is, in essence, a natural and warm material. Wood is also relatively durable and easy to work with, which has made it a favourite of builders throughout history. Our goal is to offer suitable products and quality furniture with installation and after- sales service to all of our clients. In order to achieve this, we're ready to help our clients in all stages of construction from design to production and maintenance.</p>
  <div class="btn">Read More</div>
</article>
<div class="abs tags" style="top:1178px"><span>Furniture</span><span>Windows</span><span>Doors</span><span>Staircases</span><span>Woodcarving</span><span>Graining</span></div>

<div class="abs stone-band"></div>
<article class="abs service" style="top:1266px;left:97px">
  <h3>Stone Works</h3><hr>
  <p>The natural stone found in the ground has been used in construction for centuries because of its durability. A structure built by a skilled craftsman from natural stone is unique, genuine and durable, and perfect for our bracing climate. Our experienced craftsmen are ready to help you in all stages of construction from planning to completion.</p>
  <div class="btn">Read More</div>
</article>
<div class="abs photo" style="top:1232px;left:620px;width:580px;height:292px;background:linear-gradient(100deg,#7a6a55 0%,#e4e2de 35%,#3a3a3c 65%,#9a6a42 100%)" role="img" aria-label="Stone fireplace living room, garden stone path and stacked firewood"></div>
<div class="abs tags" style="top:1556px"><span>Walls</span><span>Terraces</span><span>Paths</span><span>Outdoor kitchens</span><span>Fireplaces</span><span>Smokeries</span><span>Fences</span></div>

<div class="abs photo" style="top:1608px;left:0;width:578px;height:294px;background:linear-gradient(170deg,#a9c4de 0%,#c9d6e2 35%,#9a5a44 65%,#6c7a60 100%)" role="img" aria-label="Brick building under restoration with scaffolding and a crane, plus restored interiors"></div>
<article class="abs service" style="top:1647px;left:620px">
  <h3>Restoration</h3><hr>
  <p>It's good to see that fixing old things has become popular again in recent years and people are trying to find ways to preserve valuable old windows and pieces of furniture before deciding to replace them. It is possible to give a new life to almost any wooden door, window, piece of furniture or staircase. The extensive experience of our craftsmen will help you achieve the desired result.</p>
  <div class="btn">Read More</div>
</article>
<div class="abs tags" style="top:1923px"><span>Furniture</span><span>Windows</span><span>Doors</span><span>Staircases</span><span>Staircases</span><span>Floors</span><span>Special Projects</span></div>

<section class="abs about" role="img" aria-label="Dim photo of a craftsman at work">
  <h2 class="abs head">About Us</h2>
  <div class="abs rule"></div>
  <div class="abs brand"><i></i>Praxelun</div>
  <p class="abs">Praxelun is a company whose business operations include making wooden products, restoration and building structures from natural stone. All of our products are made by craftsmen and specialists who have extensive experience and knowledge in their fields. The products we offer are always handmade and we take the requests and ideas of the specific client into account We always strive to achieve the best possible quality.</p>
  <div class="abs sign"><b>Quality matters,</b><br>&nbsp;Praxelun</div>
</section>

<footer class="abs footer">
  <div class="abs info">
    <div class="row"><svg width="12" height="16" viewBox="0 0 12 16"><path fill="#f2672e" d="M6 0a6 6 0 0 0-6 6c0 4.5 6 10 6 10s6-5.5 6-10a6 6 0 0 0-6-6zm0 8.5A2.5 2.5 0 1 1 6 3.5a2.5 2.5 0 0 1 0 5z"/></svg><div><b>Praxelun</b><br>Keldri 12 10115 Tallinn<br>ESTONIA</div></div>
    <div class="row"><svg width="13" height="13" viewBox="0 0 24 24"><path fill="#f2672e" d="M6.6 10.8a15 15 0 0 0 6.6 6.6l2.2-2.2c.3-.3.7-.4 1-.2 1.1.4 2.3.6 3.6.6.6 0 1 .4 1 1V20c0 .6-.4 1-1 1A17 17 0 0 1 3 4c0-.6.4-1 1-1h3.5c.6 0 1 .4 1 1 0 1.3.2 2.5.6 3.6.1.3 0 .7-.2 1z"/></svg><div>+372 55 01234</div></div>
    <div class="row"><svg width="14" height="11" viewBox="0 0 14 11"><rect width="14" height="11" fill="#f2672e"/><path d="M0 0l7 6 7-6" fill="none" stroke="#111" stroke-width="1.3"/></svg><div>sales@praxelun.com</div></div>
  </div>
  <div class="abs field" style="left:413px;top:45px;width:209px;height:32px">Name</div>
  <div class="abs field" style="left:640px;top:45px;width:209px;height:32px">Email</div>
  <div class="abs field" style="left:413px;top:96px;width:209px;height:32px">Phone</div>
  <div class="abs field" style="left:640px;top:96px;width:209px;height:32px">Sublect</div>
  <div class="abs field" style="left:413px;top:148px;width:209px;height:60px">Message</div>
  <div class="abs btn submit">Submit</div>
  <div class="abs menu">
    <div style="padding-left:0;display:flex;gap:9px;align-items:center"><svg width="14" height="12" viewBox="0 0 14 12"><circle cx="3.5" cy="6" r="2.5" fill="none" stroke="#f2672e" stroke-width="1.5"/><circle cx="10.5" cy="6" r="2.5" fill="none" stroke="#f2672e" stroke-width="1.5"/></svg>Home</div>
    <div>About Us</div><div>Services</div><div>Contact Us</div>
  </div>
</footer>

<div class="abs copy">
  <p class="abs">Copyright © 2016 Praxelun. All Rights Reserved.</p>
  <div class="abs social"><i></i><i></i><i></i><i></i><i></i></div>
</div>

</body>
</html>
```